I need a business card design for a new business based in South West Australia.
I specialize in residential window cleaning & general handyman maintenance.

Dale Marsh - 412 SILVER HAWK DETAILING
- Window Cleaning
- House Maintenance

```html
<!DOCTYPE html>
<html lang="en">
<head>
<meta charset="utf-8">
<title>412 Silver Hawk Detailing – Business Card</title>
<link rel="stylesheet" href="https://fonts.googleapis.com/css2?family=Open+Sans:wght@400;600;700&display=swap">
<style>
  :root {
    --page: #eceef1;
    --card: #ffffff;
    --brand-blue: #1558b8;
    --band-top: #1a70d2;
    --band-bottom: #0c4594;
    --ink-light: #ffffff;
  }
  * { box-sizing: border-box; margin: 0; padding: 0; }
  html, body { width: 1200px; height: 900px; overflow: hidden; }
  body { background: var(--page); position: relative; font-family: "Open Sans", Arial, sans-serif; }

  .card {
    position: absolute;
    background: var(--card);
    box-shadow: 0 6px 20px rgba(0,0,0,.18);
    overflow: hidden;
  }
  .card--front { left: 78px; top: 34px; width: 588px; height: 364px; }
  .card--back  { left: 388px; top: 505px; width: 567px; height: 352px; }

  .band { position: absolute; left: 0; width: 100%;
          background: linear-gradient(180deg, var(--band-top), var(--band-bottom)); }
  .card--front .band { top: 156px; height: 208px; }
  .card--back .band  { top: 110px; height: 130px; }

  .brand { position: absolute; display: flex; align-items: center; gap: 20px; }
  .brand__mark { width: 96px; height: 96px; background: var(--brand-blue); flex: none; }
  .brand__text { display: flex; flex-direction: column; color: var(--brand-blue); }
  .brand__name { font-weight: 700; font-size: 26px; line-height: 1.15; }
  .brand__services { font-weight: 400; font-size: 14px; margin-top: 6px; }
  .card--front .brand { left: 40px; top: 30px; }

  .card--back .brand { left: 70px; top: 131px; gap: 18px; }
  .card--back .brand__mark { width: 88px; height: 88px; background: var(--ink-light); }
  .card--back .brand__text { color: var(--ink-light); }
  .card--back .brand__name { font-size: 23px; }
  .card--back .brand__services { font-size: 13px; margin-top: 4px; }

  .contact { position: absolute; left: 36px; top: 162px; color: var(--ink-light); }
  .contact__name { font-size: 24px; line-height: 1.2; }
  .contact__role { font-size: 15.5px; margin-top: 1px; }
  .contact__address { font-size: 15.5px; line-height: 21px; margin-top: 16px; }
  .contact__list { list-style: none; margin-top: 14px; font-size: 15.5px; line-height: 21px; }
  .contact__list li { display: flex; align-items: center; gap: 8px; }
  .contact__list svg { width: 13px; height: 13px; fill: var(--ink-light); flex: none; }
</style>
</head>
<body>

<section class="card card--front">
  <header class="brand">
    <div class="brand__mark"></div>
    <div class="brand__text">
      <span class="brand__name">412 Silver Hawk Detailing</span>
      <span class="brand__services">Window cleaning and house maintenance</span>
    </div>
  </header>
  <div class="band"></div>
  <div class="contact">
    <p class="contact__name">Dale Marsh</p>
    <p class="contact__role">Managing Director</p>
    <p class="contact__address">12345, Address Goes Here<br>Country Name, 123456.</p>
    <ul class="contact__list">
      <li><svg viewBox="0 0 16 16"><path d="M3.6 1.2l2.3 2.9-1.3 1.8c.9 2 2.5 3.6 4.5 4.5l1.8-1.3 2.9 2.3-1.2 2.4C7 13.6 2.4 9 1.2 3.4z"/></svg>044-555 012 345</li>
      <li><svg viewBox="0 0 16 16"><path d="M1 3h14v10H1z M2.5 4.5v.4L8 9l5.5-4.1v-.4z" fill-rule="evenodd"/></svg>hello@silverhawk.example</li>
      <li><svg viewBox="0 0 16 16"><path d="M6.5 9.5l3-3 1 1-3 3z M9 3.5l2-2a2.8 2.8 0 014 4l-2 2-1-1 2-2a1.4 1.4 0 00-2-2l-2 2z M7 12.5l-2 2a2.8 2.8 0 01-4-4l2-2 1 1-2 2a1.4 1.4 0 002 2l2-2z"/></svg>www.silverhawkdetailing.example</li>
    </ul>
  </div>
</section>

<section class="card card--back">
  <div class="band"></div>
  <header class="brand">
    <div class="brand__mark"></div>
    <div class="brand__text">
      <span class="brand__name">412 Silver Hawk Detailing</span>
      <span class="brand__services">Window cleaning and house maintenance</span>
    </div>
  </header>
</section>

</body>
</html>
```